Zvo Klinieken website for a maxillofacial surgery clinic

It's a website for a clinic for maxillofacial surgery in WordPress . The website doesn't need to be complicated but has to look professional. It needs to be in Dutch so i can give the texts. Similar websites are www.tandartsenpraktijkveldorm.nl or www.pbtspecialisten.nl. Pages would be sort of similar to https://hetcentrumvoorgezichtszorg.nl/ or https://wervelmondclinics.nl/. Those lasts are maxillofacial surgery clinic websites, but there are little more extensive.
I uploaded the logo. If this is not the proper quality i can upload the eps. Logo was made through pixelforum.

Target Market(s)

Patients who can find me and see information about the clinic

Industry/Entity Type

Healthcare

Coding

Coded - Design and coding required

Number of Pages Required

5+ page

Font styles to use
Other font styles liked:
• Something standard professional

Colors
0054AA
0677BA
7BADD7
CADEEF
E8F1F8

Requirements
Nice to have
• Something in line with the logo. I prefer a little dark like the darker logos but I'm not sure if that's professional. Logos bkvzo and rlpw are instances i'm registered to so they will have to be on the website too but small somewhere.

```html
<!DOCTYPE html>
<html lang="nl">
<head>
<meta charset="utf-8">
<title>Zvo Klinieken</title>
<link href="https://fonts.googleapis.com/css2?family=Playfair+Display:wght@700&family=Open+Sans:wght@400;600;700&display=swap" rel="stylesheet">
<style>
:root{
  --sky:#2b9fd9;
  --navy:#3c4e69;
  --navy-dark:#33435c;
  --ink:#3a4658;
  --muted:#8a919c;
  --line:#e4e8ee;
  --soft:#f6f8fb;
  --white:#fff;
}
*{box-sizing:border-box;margin:0;padding:0}
html,body{width:1200px;height:4841px;overflow:hidden}
body{position:relative;background:var(--white);font-family:"Open Sans",sans-serif;color:var(--ink)}
.abs{position:absolute}
.serif{font-family:"Playfair Display",serif;font-weight:700;color:var(--navy)}
.label{font-size:11px;color:var(--sky);text-transform:uppercase;letter-spacing:.5px;display:flex;align-items:center;gap:12px}
.label::after{content:"";width:50px;height:2px;background:var(--sky)}
.body-text{font-size:13px;line-height:24px;color:var(--muted)}
.btn{display:flex;align-items:center;justify-content:center;background:var(--sky);color:#fff;font-size:13px;font-weight:700;border-radius:4px}
.photo{background:linear-gradient(135deg,#c9d9e6,#8fb2cc)}
/* header */
.header{left:0;top:0;width:1200px;height:88px;background:#fff;border-bottom:1px solid var(--line)}
.logo-badge{left:135px;top:0;width:175px;height:98px;background:#fff;border-radius:0 0 90px 90px;box-shadow:0 6px 14px rgba(0,0,0,.12);display:flex;align-items:center;justify-content:center;gap:6px}
.logo-name{font-size:17px;font-weight:700;color:var(--sky)}
.logo-dot{width:12px;height:12px;border-radius:50%;background:var(--sky)}
.topline{top:12px;font-size:12px;color:var(--ink)}
.nav{left:338px;top:54px;display:flex;gap:22px;font-size:12px;color:var(--ink)}
.nav .active{color:var(--sky);font-weight:700}
.call{left:858px;top:0;width:200px;height:88px;background:var(--navy);color:#fff;padding:20px 0 0 46px;font-size:13px}
.call strong{display:block;font-size:19px;margin-top:4px}
.call-icon{left:858px;top:26px;width:36px;height:36px;border-radius:50%;background:#fff;display:flex;align-items:center;justify-content:center}
/* hero */
.hero{left:0;top:88px;width:1200px;height:740px}
.hero-card{left:77px;top:272px;width:603px;height:361px;background:#fff;padding:46px 46px 0 46px}
.hero-card::before{content:"";position:absolute;left:0;top:60px;width:8px;height:110px;background:var(--sky)}
.hero-card h1{font-size:56px;line-height:66px}
/* features */
.feature-card{left:90px;top:1531px;width:1016px;height:214px;background:#fff;border-radius:0 0 60px 60px;box-shadow:0 10px 24px rgba(0,0,0,.08);display:flex;padding:38px 0 0 58px;gap:58px}
.feature{display:flex;gap:14px;width:250px}
.ring{width:58px;height:58px;flex:none;border:3px solid var(--navy);border-radius:50%;display:flex;align-items:center;justify-content:center}
.feature h3{font-size:21px}
.feature .more{font-size:14px;color:var(--sky);margin:6px 0 10px}
.feature p{font-size:12px;line-height:23px;color:var(--ink)}
/* services */
.arrow-btn{width:42px;height:60px;border:1px solid var(--line);background:#fff;display:flex;align-items:center;justify-content:center;box-shadow:0 4px 10px rgba(0,0,0,.06)}
.service-text{width:278px;height:201px;background:#fff;box-shadow:0 6px 18px rgba(0,0,0,.1);padding:26px 40px}
.service-text.dark{background:var(--navy)}
.service-text h3{font-size:20px}
.service-text.dark h3,.service-text.dark p,.service-text.dark a{color:#fff}
.service-text p{font-size:12px;line-height:24px;color:var(--ink);margin:12px 0 10px}
.service-text a{font-size:14px;font-weight:700;color:var(--sky);text-decoration:none}
.outline-btn{left:513px;top:2393px;width:167px;height:45px;border:2px solid var(--navy);border-radius:4px;display:flex;align-items:center;justify-content:center;font-size:13px;font-weight:700;color:var(--navy)}
/* symmetry */
.band{left:0;top:2526px;width:1200px;height:638px;background:var(--soft)}
.point{width:264px;display:flex;gap:16px}
.point h4{font-size:14px;font-weight:700;color:var(--navy)}
.point p{font-size:12px;line-height:24px;color:var(--muted);margin-top:6px}
/* testimonials */
.t-card{width:323px;height:263px;background:#fff;box-shadow:0 4px 16px rgba(0,0,0,.1);text-align:center;padding:58px 44px 0}
.stars{color:#f0882b;font-size:18px;letter-spacing:8px}
.t-card p{font-size:12px;line-height:24px;color:var(--muted);margin-top:16px}
.avatar{width:64px;height:64px;border-radius:50%;background:linear-gradient(135deg,#d7e3ec,#8fb2cc)}
.quote{width:68px;height:34px;background:var(--navy);border-radius:34px 34px 0 0;display:flex;align-items:flex-end;justify-content:center;color:#fff;font-family:"Playfair Display",serif;font-size:30px;line-height:28px}
.t-name{font-size:17px;font-weight:700;color:var(--ink);text-align:center;width:323px}
.t-city{font-size:12px;color:var(--muted);text-align:center;width:323px}
/* contact */
.form-box{left:648px;top:3978px;width:466px;height:477px;background:#fff;border-radius:18px;padding:8px}
.form-inner{width:100%;height:100%;background:var(--navy);border-radius:14px;padding:38px 34px 0;color:#fff;text-align:center}
.form-inner h2{font-size:28px;font-weight:700}
.form-inner p{font-size:12px;line-height:18px;margin:6px 0 24px}
.field{height:44px;background:#58698a;border-radius:4px;margin-bottom:30px;text-align:left;padding:14px 22px;font-size:11px}
.submit{height:46px;background:#fff;border-radius:4px;color:var(--navy);font-size:16px;font-weight:600;display:flex;align-items:center;justify-content:center;margin-top:12px}
/* footer */
.f-title{font-size:14px;color:var(--ink);font-weight:600}
.f-list{font-size:13px;line-height:32px;color:var(--muted)}
.social{width:24px;height:24px;border-radius:50%;background:#e3e7ed}
</style>
</head>
<body>

<header>
  <div class="abs header"></div>
  <div class="abs logo-badge"><span class="logo-dot"></span><span class="logo-name">Zvo Klinieken</span></div>
  <div class="abs topline" style="left:395px">WELCOME</div>
  <div class="abs topline" style="left:629px;display:flex;gap:8px;align-items:center">
    <svg width="22" height="22" viewBox="0 0 22 22"><circle cx="11" cy="11" r="10" fill="none" stroke="#3c4e69" stroke-width="1.5"/><rect x="6" y="7.5" width="10" height="7" fill="none" stroke="#3c4e69" stroke-width="1.3"/><path d="M6 8l5 4 5-4" fill="none" stroke="#3c4e69" stroke-width="1.3"/></svg>
    info@zvoklinieken.nl</div>
  <nav class="abs nav"><span class="active">THUIS</span><span>Behandelingen</span><span>Vergoeding</span><span>Ons team</span><span>Folders</span><span>Contact Us</span></nav>
  <div class="abs call">Call us today at<strong>(020) 555-0142</strong></div>
  <div class="abs call-icon" style="left:840px"><svg width="20" height="20" viewBox="0 0 24 24"><path d="M6 3l3 1 1 4-2 2a12 12 0 006 6l2-2 4 1 1 3-2 3C10 21 3 14 3 5z" fill="none" stroke="#2b9fd9" stroke-width="1.6"/></svg></div>
</header>

<section>
  <div class="abs hero photo" role="img" aria-label="Tandarts met mondkapje behandelt een lachende patiënte" style="background:linear-gradient(120deg,#7c99ae 0%,#c6d4de 45%,#9fb6c6 100%)"></div>
  <svg class="abs" style="left:0;top:740px" width="1200" height="130" viewBox="0 0 1200 130">
    <path d="M0 60 C300 150 700 -10 1200 70 L1200 130 L0 130Z" fill="#fff"/>
    <path d="M0 60 C280 130 600 20 900 20 C1060 20 1160 50 1200 80 L1200 95 C1140 55 1040 40 900 40 C620 40 300 150 0 80Z" fill="#2b9fd9"/>
    <path d="M0 95 C300 150 700 20 1200 100" fill="none" stroke="#3c4e69" stroke-width="4"/>
  </svg>
  <div class="abs hero-card">
    <h1 class="serif">Precisiechirurgie,<br>Persoonlijke Zorg</h1>
    <p class="body-text" style="font-size:11px;line-height:20px;margin-top:20px;width:420px">Lorem ipsum dolor sit amet, consectetur adipiscing elit, sed do eiusmod tempor incididunt ut labore et dolore magna aliqua. Ut enim</p>
    <div class="btn" style="width:168px;height:46px;margin-top:26px">Meer Leren</div>
  </div>
</section>

<section>
  <div class="abs photo" role="img" aria-label="Lachend meisje in de tandartsstoel" style="left:105px;top:973px;width:302px;height:313px;border-radius:90px 0 0 0"></div>
  <div class="abs photo" role="img" aria-label="Tandarts in blauw uniform" style="left:432px;top:993px;width:118px;height:123px;background:linear-gradient(135deg,#e5ecf2,#9db9cf)"></div>
  <div class="abs photo" role="img" aria-label="Patiënte tijdens tandheelkundige behandeling" style="left:268px;top:1131px;width:304px;height:315px;border-radius:150px 0 90px 0;background:linear-gradient(135deg,#5f9fd3,#1f5f9f)"></div>
  <div class="abs" style="left:240px;top:1182px;width:96px;height:96px;border-radius:50%;background:var(--navy)"></div>
  <div class="abs label" style="left:625px;top:993px">Over ons</div>
  <h2 class="abs serif" style="left:623px;top:1026px;font-size:36px;line-height:56px">Levens Kracht Geven,<br>Een Gezicht per Keer</h2>
  <p class="abs body-text" style="left:625px;top:1155px;width:440px;font-size:12px">Lorem ipsum dolor sit amet, consectetur adipiscing elit, sed do eiusmod tempor incididunt ut labore et dolore magna aliqua. Ut enim ad min im veniam, quis nostrud exercitation ullamco laboris nisi ut aliquip ex ea commodo consequat. Duis aute irure dolor in reprehenderit in voluptate velit esse cillum dolore eu fugiat nulla pariatur. Excepteur sint occaecat cupidatat non proident, sunt in culpa qui officia deserunt mollit anim id est laborum.</p>
  <div class="abs btn" style="left:625px;top:1346px;width:168px;height:46px">Meer Leren</div>
</section>

<section class="abs feature-card">
  <div class="feature"><div class="ring"><svg width="26" height="26" viewBox="0 0 26 26"><circle cx="13" cy="13" r="9" fill="none" stroke="#3c4e69" stroke-width="2" stroke-dasharray="3 3"/></svg></div><div><h3 class="serif">Expertise</h3><div class="more">Meer Leren</div><p>Lorem ipsum dolor sit amet, consectetur adipiscing elit, se do eiusmod tempor e</p></div></div>
  <div class="feature"><div class="ring"><svg width="26" height="26" viewBox="0 0 26 26"><path d="M13 4v18M4 13h18" stroke="#3c4e69" stroke-width="2" stroke-dasharray="3 3"/></svg></div><div><h3 class="serif">Ervaring</h3><div class="more">Meer Leren</div><p>Lorem ipsum dolor sit amet, consectetur adipiscing elit, se do eiusmod tempor e</p></div></div>
  <div class="feature"><div class="ring"><svg width="26" height="26" viewBox="0 0 26 26"><path d="M6 15a7 7 0 0114 0v5H6z" fill="none" stroke="#3c4e69" stroke-width="2"/></svg></div><div><h3 class="serif">Professioneel</h3><div class="more">Meer Leren</div><p>Lorem ipsum dolor sit amet, consectetur adipiscing elit, se do eiusmod tempor e</p></div></div>
</section>

<section>
  <div class="abs label" style="left:97px;top:1853px">Diensten</div>
  <h2 class="abs serif" style="left:95px;top:1888px;font-size:40px">Onze Diensten</h2>
  <div class="abs arrow-btn" style="left:1008px;top:1870px"><svg width="12" height="14"><path d="M9 2L3 7l6 5" fill="none" stroke="#222" stroke-width="2"/></svg></div>
  <div class="abs arrow-btn" style="left:1060px;top:1870px"><svg width="12" height="14"><path d="M3 2l6 5-6 5" fill="none" stroke="#222" stroke-width="2"/></svg></div>

  <div class="abs photo" role="img" aria-label="Kaakchirurg bespreekt röntgenfoto met jonge patiënte" style="left:90px;top:1974px;width:323px;height:233px;background:linear-gradient(135deg,#b8c9c2,#516c84)"></div>
  <div class="abs photo" role="img" aria-label="Lachende vrouw in de behandelstoel" style="left:436px;top:1974px;width:323px;height:233px;background:linear-gradient(135deg,#9fd0e4,#d9a55a)"></div>
  <div class="abs photo" role="img" aria-label="Glimlachende patiënte in de behandelkamer" style="left:785px;top:1974px;width:323px;height:233px;background:linear-gradient(135deg,#dfe6ec,#a9b9c6)"></div>

  <div class="abs service-text" style="left:116px;top:2150px"><h3 class="serif">Kaakchirurgie</h3><p>Lorem ipsum dolor sit amet, consectetur adipiscing elit, sed do eiusmod tempor incididunt ut nn</p><a>Read More</a></div>
  <div class="abs service-text dark" style="left:456px;top:2150px"><h3 class="serif">Slaapgeneeskunde</h3><p>Lorem ipsum dolor sit amet, consectetur adipiscing elit, sed do eiusmod tempor incididunt ut nn</p><a>Read More</a></div>
  <div class="abs service-text" style="left:806px;top:2150px"><h3 class="serif">Plastische Chirurgie</h3><p>Lorem ipsum dolor sit amet, consectetur adipiscing elit, sed do eiusmod tempor incididunt ut nn</p><a>Read More</a></div>
  <div class="abs outline-btn">Meer Leren</div>
</section>

<section>
  <div class="abs band"></div>
  <div class="abs label" style="left:93px;top:2612px">Over ons</div>
  <h2 class="abs serif" style="left:91px;top:2646px;font-size:38px;line-height:60px">Symmetrie Vormgeven,<br>Harmonie Herstellen</h2>
  <p class="abs body-text" style="left:93px;top:2776px;width:440px;font-size:12px">Lorem ipsum dolor sit amet, consectetur adipiscing elit, sed do eiusmod tempor incididunt ut labore et dolore magna aliqua. Ut enim ad min im veniam, quis nostrud exercitation ij</p>
  <div class="abs point" style="left:104px;top:2880px"><svg width="30" height="30" viewBox="0 0 30 30"><rect x="3" y="4" width="7" height="7" fill="none" stroke="#2b9fd9" stroke-width="2"/><rect x="20" y="19" width="7" height="7" fill="none" stroke="#2b9fd9" stroke-width="2"/><path d="M10 8h13v11M7 11v12h13" fill="none" stroke="#2b9fd9" stroke-width="2"/></svg><div><h4>Klantgericht</h4><p>Lorem ipsum dolor sit amet, consectetur adipiscing elit.</p></div></div>
  <div class="abs point" style="left:372px;top:2880px"><svg width="30" height="30" viewBox="0 0 30 30"><circle cx="15" cy="6" r="3" fill="none" stroke="#2b9fd9" stroke-width="2"/><path d="M4 12h22M15 12v7l-6 8M15 19l6 8" fill="none" stroke="#2b9fd9" stroke-width="2"/></svg><div><h4>Persoonlijke Aanpak</h4><p>Lorem ipsum dolor sit amet, consectetur adipiscing elit.</p></div></div>
  <div class="abs point" style="left:104px;top:2976px"><svg width="30" height="30" viewBox="0 0 30 30"><circle cx="8" cy="11" r="3" fill="none" stroke="#2b9fd9" stroke-width="2"/><path d="M3 21a5 5 0 0110 0M16 10h11M16 15h11M16 20h8" fill="none" stroke="#2b9fd9" stroke-width="2"/></svg><div><h4>Bewezen Track Record</h4><p>Lorem ipsum dolor sit amet, consectetur adipiscing elit.</p></div></div>
  <div class="abs point" style="left:372px;top:2976px"><svg width="30" height="30" viewBox="0 0 30 30"><path d="M5 26V18M11 26V14M17 26V10M23 26V6" stroke="#2b9fd9" stroke-width="3"/></svg><div><h4>Kwaliteitsborging</h4><p>Lorem ipsum dolor sit amet, consectetur adipiscing elit.</p></div></div>
  <svg class="abs" style="left:640px;top:2614px" width="474" height="474" viewBox="0 0 474 474"><path d="M60 120 A230 230 0 0 1 440 170" fill="none" stroke="#3c4e69" stroke-width="10"/><path d="M450 200 A230 230 0 0 1 420 360" fill="none" stroke="#3c4e69" stroke-width="10"/></svg>
  <div class="abs photo" role="img" aria-label="Lachend peutermeisje" style="left:648px;top:2636px;width:458px;height:458px;border-radius:50%;background:radial-gradient(circle at 50% 45%,#e6d8cc,#8fa8b6)"></div>
</section>

<section>
  <div class="abs" style="left:0;top:3220px;width:1200px;display:flex;justify-content:center;align-items:center;gap:12px;font-size:11px;color:var(--sky)"><span style="width:50px;height:2px;background:var(--sky)"></span>GETUIGENISSEN<span style="width:50px;height:2px;background:var(--sky)"></span></div>
  <h2 class="abs serif" style="left:0;top:3250px;width:1200px;text-align:center;font-size:40px">Wat Klanten Zeggen</h2>

  <div class="abs t-card" style="left:90px;top:3392px"><div class="stars">★★★★★</div><p>Lorem ipsum dolor sit amet, consectetur adipiscing elit, sed do eiusmod tempor incididunt ut labore et dolore</p></div>
  <div class="abs t-card" style="left:441px;top:3392px"><div class="stars">★★★★★</div><p>Lorem ipsum dolor sit amet, consectetur adipiscing elit, sed do eiusmod tempor incididunt ut labore et dolore</p></div>
  <div class="abs t-card" style="left:791px;top:3392px"><div class="stars">★★★★★</div><p>Lorem ipsum dolor sit amet, consectetur adipiscing elit, sed do eiusmod tempor incididunt ut labore et dolore</p></div>

  <div class="abs avatar" role="img" aria-label="Portret van klant" style="left:219px;top:3360px"></div>
  <div class="abs avatar" role="img" aria-label="Portret van klant" style="left:570px;top:3360px"></div>
  <div class="abs avatar" role="img" aria-label="Portret van klant" style="left:920px;top:3360px"></div>

  <div class="abs quote" style="left:217px;top:3622px">“</div>
  <div class="abs quote" style="left:568px;top:3622px">“</div>
  <div class="abs quote" style="left:918px;top:3622px">“</div>

  <div class="abs t-name" style="left:90px;top:3686px">Daan Verhoef</div>
  <div class="abs t-name" style="left:441px;top:3686px">Daan Verhoef</div>
  <div class="abs t-name" style="left:791px;top:3686px">Daan Verhoef</div>
  <div class="abs t-city" style="left:90px;top:3718px">Brussels</div>
  <div class="abs t-city" style="left:441px;top:3718px">Brussels</div>
  <div class="abs t-city" style="left:791px;top:3718px">Brussels</div>
</section>

<section>
  <div class="abs photo" role="img" aria-label="Lichte praktijkruimte op de achtergrond" style="left:0;top:3897px;width:1200px;height:501px;background:linear-gradient(90deg,#b9bcbf,#dcdad6 60%,#c9c6c0)"></div>
  <div class="abs photo" role="img" aria-label="Vrouw in witte blouse kijkt op een tablet" style="left:240px;top:3765px;width:360px;height:633px;border-radius:160px 160px 0 0;background:linear-gradient(180deg,#5a4336 0%,#eae6df 30%,#d4c3a6 70%,#a98a62 100%)"></div>
  <div class="abs form-box"><div class="form-inner">
    <h2>Kom Met Ons In Contact</h2>
    <p>Lorem ipsum dolor sit amet, consectetur adipiscing elit,<br>sed do eiusmod tempor incididunt ut</p>
    <div class="field">NAAM</div>
    <div class="field">EMAIL</div>
    <div class="field">BERICHT</div>
    <div class="submit">VERSTUUR</div>
  </div></div>
</section>

<footer>
  <div class="abs" style="left:122px;top:4575px;display:flex;align-items:center;gap:8px"><span class="logo-dot"></span><span class="logo-name" style="font-size:20px">Zvo Klinieken</span></div>
  <div class="abs" style="left:113px;top:4670px;display:flex;align-items:center;gap:14px;font-size:13px;color:var(--ink)">Volg ons <span class="social"></span><span class="social"></span><span class="social"></span></div>

  <div class="abs f-title" style="left:364px;top:4552px">Snelkoppelingen</div>
  <div class="abs f-list" style="left:364px;top:4588px">Thuis<br>Behandelingen<br>Vergoeding<br>Contact us</div>

  <div class="abs f-title" style="left:586px;top:4552px">Contacteer ons</div>
  <div class="abs f-list" style="left:586px;top:4592px;line-height:24px;display:flex;gap:12px"><svg width="14" height="18" viewBox="0 0 14 18"><path d="M7 1a6 6 0 016 6c0 4-6 10-6 10S1 11 1 7a6 6 0 016-6z" fill="#2b9fd9"/><circle cx="7" cy="7" r="2" fill="#fff"/></svg><span>12 Kliniekweg<br>3521 Utrecht</span></div>
  <div class="abs f-list" style="left:586px;top:4654px;display:flex;gap:12px;align-items:center"><svg width="16" height="16" viewBox="0 0 24 24"><path d="M6 3l3 1 1 4-2 2a12 12 0 006 6l2-2 4 1 1 3-2 3C10 21 3 14 3 5z" fill="#2b9fd9"/></svg>0800-555-0199</div>
  <div class="abs f-list" style="left:586px;top:4692px;display:flex;gap:12px;align-items:center"><svg width="16" height="12" viewBox="0 0 16 12"><rect width="16" height="12" fill="#2b9fd9"/><path d="M0 0l8 6 8-6" fill="none" stroke="#fff" stroke-width="1.4"/></svg>info@zvoklinieken.nl</div>

  <div class="abs f-title" style="left:860px;top:4552px">Schrijf je in voor onze nieuwsbrief</div>
  <div class="abs" style="left:860px;top:4594px;font-size:12px;line-height:18px;color:var(--muted)">Sign up for our newsletter to<br>know the latest from us</div>
  <div class="abs" style="left:860px;top:4652px;width:146px;height:34px;border:1px solid var(--line);font-size:11px;color:var(--muted);padding:9px 18px">Email</div>
  <div class="abs" style="left:1006px;top:4652px;width:102px;height:34px;background:var(--sky);color:#fff;font-size:12px;font-weight:700;display:flex;align-items:center;justify-content:center">VERSTUUR</div>

  <div class="abs" style="left:113px;top:4770px;width:984px;height:1px;background:var(--line)"></div>
  <div class="abs" style="left:0;top:4794px;width:1200px;text-align:center;font-size:12px;color:var(--ink)">Zvo Klinieken</div>
</footer>

</body>
</html>
```